Create a business promotion flyer to leave in customer mailboxes. We are a bulk petroleum supplier, servicing any industry that requires diesel. Base in griffith NSW, servicing griffith area and surrounds.

Business Name - Terra Diesel
Fuel@terradiesel-example.com.au
Owen - 0491 570 362 ohartley@terradiesel-example.com.au
Liam - 0491 570 718 lprosser@terradiesel-example.com.au
Simon - 0491 570 905 skenway@terradiesel-example.com.au
Office 02 5550 1734

Bulk Fuel deliveries.
Oils & lubricants
Local Family owned business

```html
<!DOCTYPE html>
<html lang="en">
<head>
<meta charset="utf-8">
<title>Terra Diesel – Bulk Fuel Flyer</title>
<link rel="stylesheet" href="https://fonts.googleapis.com/css2?family=Montserrat:wght@700;800&family=Roboto:wght@400;500;700&display=swap">
<style>
  :root {
    --red: #e52420;
    --deep-red: #b5081e;
    --charcoal: #58595b;
    --ink: #231f20;
    --grey-band: #6d6e70;
    --line-grey: #8a8a8a;
    --white: #ffffff;
    --paper: #f7f7f7;
  }
  * { margin: 0; padding: 0; box-sizing: border-box; }
  html, body { width: 927px; height: 1200px; overflow: hidden; background: var(--white); }
  body { font-family: "Roboto", Arial, sans-serif; color: var(--ink); }

  .flyer { position: relative; width: 927px; height: 1200px; overflow: hidden; background: linear-gradient(#ffffff, var(--paper)); }

  .hero-photo {
    position: absolute; left: 0; top: 0; width: 927px; height: 560px;
    background:
      linear-gradient(180deg, #7fa6cf 0%, #b9cde3 30%, #dfe6ee 48%, #b7bcc2 58%, #8e9298 70%, #c9c9c9 86%, #d8d8d8 100%);
  }
  .hero-curve { position: absolute; left: 0; top: 380px; width: 927px; height: 200px; }

  .brand {
    position: absolute; top: 62px; left: 0; width: 927px;
    display: flex; justify-content: center; align-items: center; gap: 14px;
  }
  .brand-dot { width: 22px; height: 22px; border-radius: 50%; background: var(--red); }
  .brand-name { font-family: "Montserrat", Arial, sans-serif; font-weight: 800; font-size: 60px; color: var(--red); letter-spacing: -1px; }

  .headline {
    position: absolute; top: 508px; left: 0; width: 927px; text-align: center;
    font-family: "Montserrat", Arial, sans-serif; font-weight: 800; font-size: 52px; line-height: 1; letter-spacing: -0.5px;
  }
  .headline .accent { color: var(--red); }
  .headline .muted { color: var(--charcoal); }
  .subhead {
    position: absolute; top: 584px; left: 0; width: 927px; text-align: center;
    font-family: "Montserrat", Arial, sans-serif; font-weight: 800; font-size: 35px; color: var(--ink);
  }
  .intro {
    position: absolute; top: 640px; left: 106px; width: 716px;
    font-size: 26px; line-height: 35px; text-align: justify; text-align-last: center; color: var(--ink);
  }

  .services { position: absolute; top: 770px; left: 0; width: 927px; height: 170px; }
  .services-line { position: absolute; top: 40px; left: 204px; width: 538px; height: 1.5px; background: var(--line-grey); }
  .service { position: absolute; top: 0; width: 260px; text-align: center; }
  .service svg { display: block; margin: 0 auto; }
  .service-label { margin-top: 14px; font-size: 26px; line-height: 31px; font-weight: 500; color: var(--ink); }

  .footer-shape { position: absolute; left: 0; top: 950px; width: 927px; height: 250px; }

  .main-contact {
    position: absolute; top: 974px; left: 0; width: 927px;
    display: flex; justify-content: center; gap: 40px; align-items: center;
    color: var(--white); font-size: 23px;
  }
  .main-contact .item { display: flex; align-items: center; gap: 12px; }
  .badge-white { width: 34px; height: 34px; border-radius: 50%; background: var(--white); display: flex; align-items: center; justify-content: center; }

  .team { position: absolute; top: 1060px; left: 0; width: 927px; height: 108px; }
  .team-divider { position: absolute; top: 6px; width: 1px; height: 94px; background: rgba(255,255,255,0.35); }
  .member { position: absolute; top: 0; color: var(--white); }
  .member-name { font-family: "Roboto", Arial, sans-serif; font-weight: 700; font-size: 20px; margin-bottom: 12px; }
  .member-line { display: flex; align-items: center; gap: 10px; font-size: 12.5px; height: 22px; margin-bottom: 9px; white-space: nowrap; }
  .badge-red { width: 22px; height: 22px; border-radius: 50%; background: var(--deep-red); display: flex; align-items: center; justify-content: center; flex: none; }

  .base-strip {
    position: absolute; left: 0; top: 1170px; width: 927px; height: 30px; background: var(--deep-red);
    display: flex; justify-content: center; align-items: center; gap: 8px;
    color: var(--white); font-size: 13.5px; font-weight: 500; letter-spacing: 0.2px;
  }
</style>
</head>
<body>
<div class="flyer">

  <div class="hero-photo" role="img" aria-label="Photo of a white fuel tanker road train parked in front of a large steel depot shed under a blue cloudy sky"></div>

  <svg class="hero-curve" viewBox="0 0 927 200" preserveAspectRatio="none" aria-hidden="true">
    <path d="M0 160 Q240 40 463 52 Q690 40 927 160 L927 200 L0 200 Z" fill="#b5081e"/>
    <path d="M0 185 Q240 48 463 56 Q690 48 927 182 L927 200 L0 200 Z" fill="#ffffff"/>
  </svg>

  <div class="brand">
    <span class="brand-dot"></span>
    <span class="brand-name">Terra Diesel</span>
  </div>

  <h1 class="headline"><span class="accent">YOUR LOCAL</span> <span class="muted">BULK FUEL</span></h1>
  <h2 class="subhead">SUPPLIER IN GRIFFITH &amp; SURROUNDS</h2>
  <p class="intro">Terra Diesel is a trusted local supplier of high-quality bulk petroleum products, delivering dependable service with a focus on safety, efficiency and value.</p>

  <section class="services">
    <div class="services-line"></div>

    <div class="service" style="left:74px">
      <svg width="86" height="86" viewBox="0 0 86 86" aria-hidden="true">
        <circle cx="43" cy="43" r="38" fill="#fff"/>
        <path d="M43 4 A39 39 0 0 0 43 82" fill="none" stroke="#e52420" stroke-width="5"/>
        <path d="M43 4 A39 39 0 0 1 43 82" fill="none" stroke="#6d6e70" stroke-width="5"/>
        <rect x="30" y="24" width="26" height="38" rx="4" fill="none" stroke="#e52420" stroke-width="2"/>
        <line x1="30" y1="32" x2="56" y2="32" stroke="#e52420" stroke-width="2"/>
        <path d="M43 39 C39 45 38 48 38 50 A5 5 0 0 0 48 50 C48 48 47 45 43 39 Z" fill="none" stroke="#e52420" stroke-width="2"/>
      </svg>
      <div class="service-label">Bulk Fuel deliveries</div>
    </div>

    <div class="service" style="left:343px">
      <svg width="86" height="86" viewBox="0 0 86 86" aria-hidden="true">
        <circle cx="43" cy="43" r="38" fill="#fff"/>
        <path d="M43 4 A39 39 0 0 0 43 82" fill="none" stroke="#e52420" stroke-width="5"/>
        <path d="M43 4 A39 39 0 0 1 43 82" fill="none" stroke="#6d6e70" stroke-width="5"/>
        <path d="M32 34 L46 30 L54 36 L54 60 L32 60 Z" fill="none" stroke="#e52420" stroke-width="2" stroke-linejoin="round"/>
        <rect x="38" y="25" width="8" height="5" fill="none" stroke="#e52420" stroke-width="2"/>
        <circle cx="28" cy="22" r="2" fill="#e52420"/>
        <circle cx="34" cy="19" r="1.5" fill="#e52420"/>
      </svg>
      <div class="service-label">Oils &amp; lubricants</div>
    </div>

    <div class="service" style="left:612px">
      <svg width="86" height="86" viewBox="0 0 86 86" aria-hidden="true">
        <circle cx="43" cy="43" r="38" fill="#fff"/>
        <path d="M43 4 A39 39 0 0 0 43 82" fill="none" stroke="#e52420" stroke-width="5"/>
        <path d="M43 4 A39 39 0 0 1 43 82" fill="none" stroke="#6d6e70" stroke-width="5"/>
        <path d="M43 34 C36 28 30 32 33 38 L43 46 L53 38 C56 32 50 28 43 34 Z" fill="none" stroke="#e52420" stroke-width="2" stroke-linejoin="round"/>
        <path d="M24 46 L32 58 L43 60 L54 58 L62 46" fill="none" stroke="#e52420" stroke-width="2" stroke-linecap="round" stroke-linejoin="round"/>
      </svg>
      <div class="service-label">Local Family<br>owned business</div>
    </div>
  </section>

  <svg class="footer-shape" viewBox="0 0 927 250" preserveAspectRatio="none" aria-hidden="true">
    <rect x="0" y="0" width="927" height="250" fill="#6d6e70"/>
    <path d="M0 0 H927 V74 Q470 104 0 56 Z" fill="#b5081e"/>
    <path d="M0 56 Q470 104 927 74 L927 84 Q470 122 0 78 Z" fill="#ffffff"/>
  </svg>

  <div class="main-contact">
    <div class="item">
      <span class="badge-white"><svg width="16" height="12" viewBox="0 0 16 12" aria-hidden="true"><rect width="16" height="12" rx="2" fill="#b5081e"/><path d="M1 1 L8 7 L15 1" fill="none" stroke="#fff" stroke-width="1.5"/></svg></span>
      <span>Fuel@terradiesel-example.com.au</span>
    </div>
    <div class="item">
      <span class="badge-white"><svg width="16" height="16" viewBox="0 0 24 24" aria-hidden="true"><path d="M6.6 10.8a15.1 15.1 0 0 0 6.6 6.6l2.2-2.2a1 1 0 0 1 1-.25 11.4 11.4 0 0 0 3.6.57 1 1 0 0 1 1 1V20a1 1 0 0 1-1 1A17 17 0 0 1 3 4a1 1 0 0 1 1-1h3.5a1 1 0 0 1 1 1c0 1.25.2 2.45.57 3.57a1 1 0 0 1-.25 1z" fill="#b5081e"/></svg></span>
      <span>02 5550 1734</span>
    </div>
  </div>

  <section class="team">
    <div class="team-divider" style="left:322px"></div>
    <div class="team-divider" style="left:608px"></div>

    <div class="member" style="left:60px">
      <div class="member-name">OWEN</div>
      <div class="member-line"><span class="badge-red"><svg width="11" height="11" viewBox="0 0 24 24"><path d="M6.6 10.8a15.1 15.1 0 0 0 6.6 6.6l2.2-2.2a1 1 0 0 1 1-.25 11.4 11.4 0 0 0 3.6.57 1 1 0 0 1 1 1V20a1 1 0 0 1-1 1A17 17 0 0 1 3 4a1 1 0 0 1 1-1h3.5a1 1 0 0 1 1 1c0 1.25.2 2.45.57 3.57a1 1 0 0 1-.25 1z" fill="#fff"/></svg></span>0491 570 362</div>
      <div class="member-line"><span class="badge-red"><svg width="11" height="8" viewBox="0 0 16 12"><rect width="16" height="12" rx="2" fill="#fff"/><path d="M1 1 L8 7 L15 1" fill="none" stroke="#b5081e" stroke-width="1.5"/></svg></span>ohartley@terradiesel-example.com.au</div>
    </div>

    <div class="member" style="left:345px">
      <div class="member-name">LIAM</div>
      <div class="member-line"><span class="badge-red"><svg width="11" height="11" viewBox="0 0 24 24"><path d="M6.6 10.8a15.1 15.1 0 0 0 6.6 6.6l2.2-2.2a1 1 0 0 1 1-.25 11.4 11.4 0 0 0 3.6.57 1 1 0 0 1 1 1V20a1 1 0 0 1-1 1A17 17 0 0 1 3 4a1 1 0 0 1 1-1h3.5a1 1 0 0 1 1 1c0 1.25.2 2.45.57 3.57a1 1 0 0 1-.25 1z" fill="#fff"/></svg></span>0491 570 718</div>
      <div class="member-line"><span class="badge-red"><svg width="11" height="8" viewBox="0 0 16 12"><rect width="16" height="12" rx="2" fill="#fff"/><path d="M1 1 L8 7 L15 1" fill="none" stroke="#b5081e" stroke-width="1.5"/></svg></span>lprosser@terradiesel-example.com.au</div>
    </div>

    <div class="member" style="left:632px">
      <div class="member-name">SIMON</div>
      <div class="member-line"><span class="badge-red"><svg width="11" height="11" viewBox="0 0 24 24"><path d="M6.6 10.8a15.1 15.1 0 0 0 6.6 6.6l2.2-2.2a1 1 0 0 1 1-.25 11.4 11.4 0 0 0 3.6.57 1 1 0 0 1 1 1V20a1 1 0 0 1-1 1A17 17 0 0 1 3 4a1 1 0 0 1 1-1h3.5a1 1 0 0 1 1 1c0 1.25.2 2.45.57 3.57a1 1 0 0 1-.25 1z" fill="#fff"/></svg></span>0491 570 905</div>
      <div class="member-line"><span class="badge-red"><svg width="11" height="8" viewBox="0 0 16 12"><rect width="16" height="12" rx="2" fill="#fff"/><path d="M1 1 L8 7 L15 1" fill="none" stroke="#b5081e" stroke-width="1.5"/></svg></span>skenway@terradiesel-example.com.au</div>
    </div>
  </section>

  <div class="base-strip">
    <svg width="11" height="15" viewBox="0 0 12 16" aria-hidden="true"><path d="M6 1a5 5 0 0 0-5 5c0 3.8 5 9 5 9s5-5.2 5-9a5 5 0 0 0-5-5z" fill="none" stroke="#fff" stroke-width="1.6"/><circle cx="6" cy="6" r="1.8" fill="#fff"/></svg>
    <span>BASED IN GRIFFITH NSW SERVICING GRIFFITH AREA &amp; SURROUNDS</span>
  </div>

</div>
</body>
</html>
```